Business Card Design

We are a non profit organization that holds 10 days of races and car shows to raise money for autism. We stage the largest vintage race event in the country and the only one held on city streets.

We need business cards for myself and for 100 volunteers that stage the event. We like our cards to look exciting and to capture the essence of vintage racing.

Target Market(s)

sponsors and volunteers - most in the auto industry. This is not a TRELWAY crowd

Industry/Entity Type

Non Profit

Contact Information for Business Card

Marcus Hollenbeck
Executive Director
Ridgeway Classic Motor Rally Society
2740 Orchard Lane, Suite 318
Pittsburgh, PA 15907
hollenbeck@rcmrs-example.org
cell 555 013-7482
www.rcmrs-example.org

Font styles to use
Sans Serif

Colors
ec2027

Requirements
Must have
• our logo place a car image.Could place racing image on back of card along with website

Must include this statement small somewhere:
Benefitting the Hearthline Families Network and Brookmere Learning Center

```html
<!DOCTYPE html>
<html lang="en">
<head>
<meta charset="utf-8">
<title>Ridgeway Classic Motor Rally Society – Business Cards</title>
<link rel="stylesheet" href="https://fonts.googleapis.com/css2?family=Montserrat:wght@400;600;700&display=swap">
<style>
  :root{
    --red:#ec2027;
    --red-deep:#c81a20;
    --charcoal:#2e2e30;
    --charcoal-deep:#1f1f21;
    --white:#ffffff;
    --paper:#f2f2f2;
    --stage:#d9d9db;
    --muted:#b9b9bc;
  }
  *{margin:0;padding:0;box-sizing:border-box}
  html,body{width:1200px;height:988px;overflow:hidden}
  body{
    background:var(--stage);
    font-family:"Montserrat",sans-serif;
    display:flex;flex-direction:column;align-items:center;justify-content:center;gap:32px;
  }
  .card{
    position:relative;width:780px;height:446px;overflow:hidden;
    box-shadow:0 10px 28px rgba(0,0,0,.25);
  }
  .card-art{position:absolute;inset:0;width:100%;height:100%}

  .racing-image{
    position:absolute;left:160px;top:232px;width:600px;height:194px;
    background:linear-gradient(100deg,var(--red-deep) 0%,#8f1217 55%,var(--charcoal-deep) 100%);
    opacity:.9;
  }

  .identity{position:absolute;left:48px;top:150px;color:var(--white)}
  .identity-name{font-size:26px;font-weight:700;letter-spacing:2px;text-transform:uppercase}
  .identity-role{font-size:11px;font-weight:400;letter-spacing:3px;text-transform:uppercase;margin-top:4px;opacity:.85}
  .contacts{
    position:absolute;left:48px;top:212px;width:470px;
    display:grid;grid-template-columns:200px 1fr;row-gap:10px;column-gap:20px;
    color:var(--white);font-size:12px;
  }
  .contact{display:flex;align-items:center;gap:8px;white-space:nowrap}
  .contact-icon{width:18px;height:18px;flex:none}
  .contact-address{grid-column:1 / span 2}
  .org-mark{
    position:absolute;right:38px;top:208px;width:230px;
    display:flex;align-items:center;gap:12px;
  }
  .org-mark-circle{width:70px;height:70px;border-radius:50%;background:var(--white);flex:none}
  .org-mark-name{color:var(--white);font-size:13px;font-weight:600;line-height:1.3;text-transform:uppercase;letter-spacing:1px}
  .benefit-note{
    position:absolute;left:48px;top:318px;width:520px;
    color:var(--muted);font-size:10px;font-weight:400;letter-spacing:.5px;line-height:1.4;
  }
</style>
</head>
<body>

  <!-- Back of card -->
  <section class="card card-back">
    <svg class="card-art" viewBox="0 0 780 446" preserveAspectRatio="none" aria-hidden="true">
      <rect width="780" height="446" fill="var(--red)"/>
      <rect width="780" height="200" fill="var(--paper)"/>
      <polygon points="0,176 70,176 130,230 0,230" fill="var(--charcoal)"/>
      <polygon points="0,200 60,200 100,230 0,230" fill="var(--charcoal-deep)"/>
    </svg>
    <div class="racing-image" role="img" aria-label="Vintage race car photograph"></div>
  </section>

  <!-- Front of card -->
  <section class="card card-front">
    <svg class="card-art" viewBox="0 0 780 446" preserveAspectRatio="none" aria-hidden="true">
      <rect width="780" height="446" fill="var(--charcoal)"/>
      <polygon points="0,0 780,0 780,290 0,290" fill="var(--red)"/>
      <polygon points="250,0 330,0 390,48 300,48" fill="var(--charcoal)"/>
      <polygon points="290,0 330,0 370,32 320,32" fill="var(--red-deep)"/>
      <polygon points="620,446 700,446 780,380 780,360 690,400" fill="var(--white)"/>
    </svg>

    <div class="identity">
      <div class="identity-name">Marcus Hollenbeck</div>
      <div class="identity-role">Executive Director</div>
    </div>

    <div class="contacts">
      <div class="contact">
        <svg class="contact-icon" viewBox="0 0 18 18"><circle cx="9" cy="9" r="8" fill="none" stroke="#fff" stroke-width="1.3"/><path d="M6 5l2 0 .8 2-1 .8a5 5 0 0 0 2.4 2.4l.8-1 2 .8v2c-4 .3-7.3-3-7-7z" fill="#fff"/></svg>
        555 013-7482
      </div>
      <div class="contact">
        <svg class="contact-icon" viewBox="0 0 18 18"><circle cx="9" cy="9" r="8" fill="none" stroke="#fff" stroke-width="1.3"/><rect x="5" y="6" width="8" height="6" fill="none" stroke="#fff" stroke-width="1.1"/><path d="M5 6l4 3 4-3" fill="none" stroke="#fff" stroke-width="1.1"/></svg>
        hollenbeck@rcmrs-example.org
      </div>
      <div class="contact">
        <svg class="contact-icon" viewBox="0 0 18 18"><circle cx="9" cy="9" r="8" fill="none" stroke="#fff" stroke-width="1.3"/><rect x="6.5" y="4.5" width="5" height="9" rx="1" fill="none" stroke="#fff" stroke-width="1.1"/></svg>
        555 013-7482
      </div>
      <div class="contact">
        <svg class="contact-icon" viewBox="0 0 18 18"><circle cx="9" cy="9" r="8" fill="none" stroke="#fff" stroke-width="1.3"/><circle cx="9" cy="9" r="4" fill="none" stroke="#fff" stroke-width="1.1"/><path d="M5 9h8M9 5v8" stroke="#fff" stroke-width=".9"/></svg>
        www.rcmrs-example.org
      </div>
      <div class="contact contact-address">
        <svg class="contact-icon" viewBox="0 0 18 18"><circle cx="9" cy="9" r="8" fill="none" stroke="#fff" stroke-width="1.3"/><path d="M9 14s-3.5-3.6-3.5-6a3.5 3.5 0 0 1 7 0c0 2.4-3.5 6-3.5 6z" fill="#fff"/><circle cx="9" cy="8" r="1.2" fill="var(--red)"/></svg>
        2740 Orchard Lane, Suite 318
      </div>
    </div>

    <div class="org-mark">
      <span class="org-mark-circle"></span>
      <span class="org-mark-name">Ridgeway Classic Motor Rally Society</span>
    </div>

    <p class="benefit-note">Benefitting the Hearthline Families Network and Brookmere Learning Center</p>
  </section>

</body>
</html>
```